Quill Harbor (IT/Network Services)

Quill Harbor, LLC provides technology services to small and medium businesses. Essentially, anytime you've every thought your business might need an "IT guy" to handle something you could instead call us to handle it. Basically, you can outsource your IT needs to us.

This is a brand new company and so we'll need a brand new website. I'd like to use WordPress to handle the site since that will make things easier for me to maintain in the long run.

The site should include a, more-or-less, static front page with the dynamic data occurring on pages linked from a navigational area.

I have a logo already designed that I would like to see used in the design. The one with "white" in the title is the official logo, just added some other versions for your perusal.

Color queues from the logo but feel free to add other colors where applicable.

The site should feel somewhat corporate but with a "younger" slant (something a 25-35 year old would enjoy).

Pages (either to be added initially or by me after design completion):
"About" section - includes company history, business philosophy, etc.
"Services" section - service options, service approach, service specifics
"Testimonials" section - (eventually)
"News" section - (eventually) industry news, company news, events, blog
Contact Links

Websites to view:
The two largest local competitors:
http://www.brightmarsh-tech.example/
http://www.kelvarworks.example/
Other local competitors:
http://www.tpbllc.example/
http://www.morrowfield.example/

Other info you might find useful:
Domain: qhllc.example
Address:
417 Elm Row S
Suite 512B
Nashville, TN 37288
Phone: 615-555-0187
Emails available for use/display:
info@qhllc.example
sales@qhllc.example

Target Market(s)

Our target clients are mainly small businesses (25 or less computer users) which means we're looking at a lot of start-ups or younger companies. We'll be interacting with many entrepreneurs and young business owners.

Requirements
Must have
• Need full WP theme (not a mockup)

```html
<!DOCTYPE html>
<html lang="en">
<head>
<meta charset="utf-8">
<title>Quill Harbor — IT &amp; Network Services</title>
<link rel="stylesheet" href="https://fonts.googleapis.com/css2?family=Arimo:wght@400;700&family=PT+Sans:wght@400&family=Questrial&family=Cinzel:wght@400&display=swap">
<style>
  :root{
    --orange:#f39200;
    --orange-dark:#e08600;
    --ink:#333;
    --text:#555;
    --muted:#888;
    --grey-logo:#7b7b7b;
    --panel:#ffffff;
    --header-bg:#f4f4f4;
    --frame:#6e6e6e;
    --stripe:#e9e9e9;
    --footer-text:#e6e6e6;
    --title-red:#9a2a22;
  }
  *{box-sizing:border-box;margin:0;padding:0}
  html,body{width:1110px;height:1200px;overflow:hidden}
  body{
    background:linear-gradient(180deg,#050505 0%,#3a3b3c 35%,#6f7275 70%,#7d8083 100%);
    font-family:"Arimo",Arial,sans-serif;color:var(--text);
  }
  .stage{position:absolute;left:0;top:0;width:1040px;height:1125px;transform:scale(1.0673,1.0667);transform-origin:0 0}
  .abs{position:absolute}
  .page{left:34px;top:9px;width:969px;height:1014px;background:var(--panel);border-radius:5px;box-shadow:0 2px 6px rgba(0,0,0,.5);overflow:hidden}
  .masthead{left:0;top:0;width:969px;height:141px;background:linear-gradient(180deg,#fafafa,#f0f0f0);border-bottom:1px solid #e2e2e2}
  .brand{left:28px;top:34px;display:flex;align-items:center;gap:16px}
  .brand-dot{width:70px;height:70px;border-radius:50%;background:var(--orange)}
  .brand-name{font-family:"Questrial",sans-serif;font-size:44px;color:var(--grey-logo);letter-spacing:1px}
  .search{left:702px;top:25px;width:255px;height:30px;border:1px solid #bbb;border-radius:15px;background:linear-gradient(180deg,#fff,#e8e8e8);font-size:11px;color:#777;padding:8px 26px}
  .search svg{position:absolute;right:12px;top:5px}
  .phone{left:717px;top:65px;display:flex;align-items:center;gap:8px}
  .phone-icon{width:32px;height:28px;border-radius:4px;background:linear-gradient(180deg,#e6e6e6,#bdbdbd)}
  .phone-num{font-size:18px;color:var(--orange)}
  .nav{left:424px;top:110px;display:flex;gap:0;font-size:13px;color:var(--ink)}
  .nav a{color:inherit;text-decoration:none;padding:5px 0;margin-right:26px}
  .nav a.current{background:var(--orange);color:#222;border-radius:8px;padding:5px 22px;margin-right:12px}
  .slide-text h2{font-family:"Cinzel",serif;font-weight:400;font-size:20px;color:var(--title-red);left:642px;top:238px;position:absolute}
  .slide-text p{position:absolute;left:583px;top:293px;width:340px;font-size:12.5px;line-height:24px;color:#333}
  .box{width:243px;background:linear-gradient(180deg,#fff,#eee);border-radius:5px;overflow:hidden}
  .box-head{height:30px;background:var(--orange);font-size:14px;color:#111;padding:7px 27px;text-transform:uppercase}
  .box-foot{position:absolute;left:0;bottom:0;width:100%;height:10px;background:var(--orange)}
  .item{padding:12px 0 0 17px;font-size:10.5px;line-height:16px;color:var(--muted)}
  .item .date{color:#333;font-size:11px;margin-bottom:5px}
  .rule{border-top:1px dotted #777;margin:8px 6px 0}
  .more{position:absolute;right:9px;font-size:11px;color:#111}
  .avatar{position:absolute;left:10px;width:46px;height:52px;background:linear-gradient(180deg,#d9cfc6,#3a3a3a);border-radius:2px}
  .testi{position:absolute;left:63px;font-size:10.5px;line-height:16px;color:var(--muted)}
  .testi .date{color:#333;font-size:11px;margin-bottom:5px}
  .welcome{left:293px;top:540px;font-family:"PT Sans",sans-serif;font-size:23px;color:#222}
  .welcome-rule{left:296px;top:572px;width:236px;border-top:1px dotted #333}
  .intro{left:294px;top:592px;width:650px;font-size:11.5px;line-height:21px;color:#444}
  .feature h3{position:absolute;font-family:"PT Sans",sans-serif;font-weight:400;font-size:17px;color:#222}
  .feature .shot{position:absolute;width:266px;height:105px;border:1px solid #e3e3e3}
  .feature p{position:absolute;width:225px;font-size:10.5px;line-height:18px;color:#444}
  .feature .read{position:absolute;font-size:11px;color:var(--orange);text-decoration:none}
  .footer-title{left:48px;top:1043px;font-size:14px;color:#d6d6d6}
  .signup{left:43px;top:1074px;width:181px;height:29px;display:flex}
  .signup span{flex:1;background:linear-gradient(180deg,#f5f5f5,#cfcfcf);border-radius:3px 0 0 3px}
  .signup b{width:27px;background:var(--orange);font-size:11px;color:#222;display:flex;align-items:center;justify-content:center;border-radius:0 3px 3px 0}
  .legal{left:430px;top:1047px;width:305px;text-align:center;font-size:11px;color:var(--footer-text);line-height:24px}
  .social{left:853px;top:1068px;display:flex;gap:9px}
  .social span{width:23px;height:21px;border-radius:3px;background:#3e8fd0}
  .social span:last-child{background:var(--orange)}
</style>
</head>
<body>
<div class="stage">
  <div class="abs page">
    <header class="abs masthead">
      <div class="abs brand"><span class="brand-dot"></span><span class="brand-name">Quill Harbor</span></div>
      <div class="abs search">Search
        <svg width="20" height="20" viewBox="0 0 20 20"><circle cx="8" cy="8" r="6" fill="none" stroke="#666" stroke-width="2"/><line x1="12.5" y1="12.5" x2="18" y2="18" stroke="#666" stroke-width="3"/></svg>
      </div>
      <div class="abs phone"><span class="phone-icon"></span><span class="phone-num">236 555 0142</span></div>
      <nav class="abs nav">
        <a class="current" href="#">Home</a><a href="#">Services</a><a href="#">Benefits</a><a href="#">Careers</a><a href="#">Newsroom</a><a href="#">Blog</a><a href="#" style="margin-right:0">Contact</a>
      </nav>
    </header>

    <section class="slider">
      <svg class="abs" style="left:0;top:150px" width="969" height="400" viewBox="0 0 969 400">
        <defs>
          <radialGradient id="shade" cx="0.5" cy="0.5" r="0.5"><stop offset="0" stop-color="#000" stop-opacity=".35"/><stop offset="1" stop-color="#000" stop-opacity="0"/></radialGradient>
          <linearGradient id="photo" x1="0" x2="1"><stop offset="0" stop-color="#e8ecec"/><stop offset=".5" stop-color="#9aa0a0"/><stop offset="1" stop-color="#d9dcdc"/></linearGradient>
        </defs>
        <ellipse cx="360" cy="368" rx="340" ry="16" fill="url(#shade)"/>
        <path d="M17 52 Q484 -10 957 52 L957 352 L17 352 Z" fill="var(--frame)"/>
        <path d="M32 58 Q484 4 947 58 L947 336 L32 336 Z" fill="var(--stripe)"/>
        <path d="M32 58 Q280 22 556 18 L556 336 L32 336 Z" fill="url(#photo)" role="img" aria-label="Photo of a support agent with a headset at a desk of computer monitors"/>
        <circle cx="35" cy="194" r="10" fill="#eee" stroke="#999"/><path d="M38 189 L33 194 L38 199" fill="none" stroke="#333" stroke-width="2"/>
        <circle cx="942" cy="194" r="10" fill="#eee" stroke="#999"/><path d="M939 189 L944 194 L939 199" fill="none" stroke="#333" stroke-width="2"/>
        <g fill="#999" stroke="#666" stroke-width=".5">
          <circle cx="507" cy="325" r="4.5"/><circle cx="522" cy="325" r="4.5"/><circle cx="537" cy="325" r="4.5" fill="var(--orange)"/><circle cx="552" cy="325" r="4.5"/><circle cx="567" cy="325" r="4.5"/><circle cx="582" cy="325" r="4.5"/>
        </g>
      </svg>
      <div class="slide-text">
        <h2>TECHNOLOGY</h2>
        <p>Lorem ipsum dolor sit amet, consectetuer adipiscing elit, sed diam nonummy nibh euismod tincidunt ut laoreet dolore magna aliquam erat volutpat. Lorem ipsum dolor sit amet, consectetuer adipiscing elit, sed diam nonummy nibh euismod tincidunt.</p>
      </div>
    </section>

    <aside>
      <div class="abs box" style="left:17px;top:527px;height:221px">
        <div class="box-head">Latest News</div>
        <div class="item"><div class="date">May 23, 2012</div>Nunc varius facilisis eros. Sed erat. In in velit quis arcu orne laoreet. Curabitur adipiscing luctus massa.</div>
        <div class="rule"></div>
        <div class="item" style="padding-top:8px"><div class="date">May 23, 2012</div>Nunc varius facilisis eros. Sed erat. In in velit quis arcu orne laoreet. Curabitur adipiscing luctus massa.</div>
        <span class="more" style="top:196px">View More &gt;&gt;</span>
        <div class="box-foot"></div>
      </div>
      <div class="abs box" style="left:17px;top:768px;height:221px">
        <div class="box-head">Testimonials</div>
        <div class="avatar" style="top:45px" role="img" aria-label="Portrait of a client"></div>
        <div class="testi" style="top:43px"><div class="date">May 23, 2012</div>Nunc varius facilisis eros. Sed erat.<br>In in velit quis arcu orne laoreet.</div>
        <div class="rule" style="position:absolute;top:100px;left:0;right:0"></div>
        <div class="avatar" style="top:116px" role="img" aria-label="Portrait of a client"></div>
        <div class="testi" style="top:122px"><div class="date">May 23, 2012</div>Nunc varius facilisis eros. Sed erat.<br>In in velit quis arcu orne laoreet.</div>
        <span class="more" style="top:190px">View More &gt;&gt;</span>
        <div class="box-foot"></div>
      </div>
    </aside>

    <main>
      <h1 class="abs welcome" style="font-weight:400">Welcome to Our Site</h1>
      <div class="abs welcome-rule"></div>
      <p class="abs intro">Nunc varius facilisis eros. Sed erat. In in velit quis arcu ornare laoreet. Curabitur adipiscing luctus massa.Integer ut purus ac commodo Nunc varius facilisis eros. Sed erat. Nunc varius facilisis eros. Sed erat. In in velit quis arcu ornare laoreet. Curabitur adipiscing luctus massa.Integer ut purus ac commodo Nunc varius facilisis eros. Sed erat.</p>

      <div class="feature">
        <h3 style="left:300px;top:691px">People</h3>
        <div class="shot" style="left:288px;top:728px;background:radial-gradient(ellipse at 50% 45%,#6fa8dc 0,#c9d9ea 35%,#fff 70%)" role="img" aria-label="Illustration of coloured figures around a globe"></div>
        <p style="left:302px;top:859px">Nunc varius facilisis eros. Sed erat. In in velit quis arcu ornare laoreet. Curabitur adipiscing luctus massa.Integer ut purus ac commodo Nunc varius facilisis eros.</p>
        <a class="read" style="left:302px;top:942px" href="#">Read More</a>

        <h3 style="left:641px;top:691px">Perspective</h3>
        <div class="shot" style="left:639px;top:728px;background:radial-gradient(ellipse at 50% 50%,#d8d8d8 0,#f0f0f0 40%,#fff 70%)" role="img" aria-label="Illustration of puzzle pieces with an email symbol"></div>
        <p style="left:643px;top:859px">Nunc varius facilisis eros. Sed erat. In in velit quis arcu ornare laoreet. Curabitur adipiscing luctus massa.Integer ut purus ac commodo Nunc varius facilisis eros.</p>
        <a class="read" style="left:643px;top:942px" href="#">Read More</a>
      </div>
    </main>
  </div>

  <footer>
    <div class="abs footer-title">Sign up to our newsletter!</div>
    <div class="abs signup"><span></span><b>GO</b></div>
    <div class="abs legal">Privacy &amp; Legal &nbsp;|&nbsp; Site Map &nbsp;|&nbsp; Contact Us<br>© 2012 Quill Harbor. All rights reserved</div>
    <div class="abs social"><span></span><span></span><span></span><span></span><span></span></div>
  </footer>
</div>
</body>
</html>
```